Lorvex Tilo medical cannibis cultivation company

tag - Tilo rise
Lorvex Tilo medical cannabis cultivation - logo is selected- can we please see bold examples with our selection. We are mainly dealing with medical companies and professionals. We would like to be stand out in the crowd with our designs. Welcome any and all attempts. Thanks

Target Market(s)

Medical and Professional

Industry/Entity Type

Medical And Science

Font styles to use
Sans Serif

Colors

Designer to choose colors to be used in the design.

Requirements
Must have
• Bright colour and be bold- Love the teal and magenta that is currently on the dark background design.
Nice to have
• shading and the 3D affect- The shadowed appearance.
Should not have
• Anything related to illegal activity or un professional manners

```html
<!DOCTYPE html>
<html lang="en">
<head>
<meta charset="utf-8">
<title>Lorvex Tilo – Business Card</title>
<link href="https://fonts.googleapis.com/css2?family=Roboto:wght@400;500;700&display=swap" rel="stylesheet">
<style>
  :root {
    --backdrop: #e4e4e4;
    --card-black: #000000;
    --magenta: #9d4d99;
    --teal: #00a9e6;
    --ring-grey: #8a8f96;
    --text-light: #f4eef5;
    --white: #ffffff;
  }
  * { margin: 0; padding: 0; box-sizing: border-box; }
  html, body {
    width: 1125px; height: 1200px; overflow: hidden;
    background: var(--backdrop);
    font-family: "Roboto", Arial, sans-serif;
  }
  .card {
    position: absolute;
    left: 150px; width: 795px; height: 457px;
    background: var(--card-black);
    border-radius: 28px;
    overflow: hidden;
  }
  .card--front { top: 96px; }
  .card--back { top: 612px; }
  .band { position: absolute; inset: 0; width: 795px; height: 457px; }

  .brand { position: absolute; left: 50px; top: 46px; width: 264px; text-align: center; }
  .brand__ring {
    width: 150px; height: 150px; margin: 0 auto 10px;
    border: 5px solid var(--ring-grey); border-radius: 50%;
  }
  .brand__name {
    color: var(--teal); font-weight: 500; font-size: 38px;
    letter-spacing: 0.5px; line-height: 1; white-space: nowrap;
  }
  .brand__tag {
    display: flex; align-items: center; gap: 8px; margin-top: 4px;
    color: #c9c9c9; font-size: 17px; letter-spacing: 2px;
  }
  .brand__tag::before, .brand__tag::after {
    content: ""; flex: 1; height: 2px; background: #b8b8b8;
  }

  .contact { position: absolute; right: 44px; top: 220px; text-align: right; color: var(--text-light); }
  .contact__name { font-size: 28px; font-weight: 700; letter-spacing: 0.5px; color: var(--white); line-height: 1.1; }
  .contact__role { font-size: 19px; font-weight: 500; line-height: 1.2; }
  .contact__address { margin-top: 14px; font-size: 18px; line-height: 25px; }
  .contact__lines { margin-top: 10px; font-size: 18px; line-height: 26px; }
  .contact__line { display: flex; justify-content: flex-end; align-items: center; gap: 10px; }
  .contact__line svg { width: 17px; height: 17px; fill: var(--white); }

  .back-mark {
    position: absolute; left: 270px; top: 100px; width: 256px; height: 256px;
    border: 6px solid var(--ring-grey); border-radius: 50%;
    display: flex; align-items: center; justify-content: center;
  }
  .back-mark__name { color: var(--teal); font-weight: 500; font-size: 32px; white-space: nowrap; }
  .back-url {
    position: absolute; left: 0; right: 0; top: 392px; text-align: center;
    color: var(--white); font-size: 19px; letter-spacing: 5px;
  }
</style>
</head>
<body>
  <section class="card card--front">
    <svg class="band" viewBox="0 0 795 457" aria-hidden="true">
      <path fill="var(--teal)" d="M0,372 C260,360 500,230 795,168 L795,457 L0,457 Z"/>
      <path fill="var(--magenta)" d="M0,386 C260,376 500,252 795,188 L795,457 L0,457 Z"/>
    </svg>

    <div class="brand">
      <div class="brand__ring"></div>
      <div class="brand__name">LORVEX TILO</div>
      <div class="brand__tag">TILO RISE</div>
    </div>

    <div class="contact">
      <div class="contact__name">MAREN HOLT</div>
      <div class="contact__role">CEO/FOUNDER</div>
      <div class="contact__address">4210 Cedarfield Road<br>Juneau, Alaska 34821</div>
      <div class="contact__lines">
        <div class="contact__line">614 208 3915
          <svg viewBox="0 0 24 24"><path d="M6.6 10.8a15.1 15.1 0 0 0 6.6 6.6l2.2-2.2c.3-.3.7-.4 1-.2 1.1.4 2.3.6 3.6.6.6 0 1 .4 1 1V20c0 .6-.4 1-1 1A17 17 0 0 1 3 4c0-.6.4-1 1-1h3.5c.6 0 1 .4 1 1 0 1.3.2 2.5.6 3.6.1.3 0 .7-.2 1z"/></svg>
        </div>
        <div class="contact__line">maren@lorvextilo.com
          <svg viewBox="0 0 24 24"><path d="M2 5h20v14H2z M3 6l9 7 9-7" fill="var(--white)" stroke="var(--magenta)" stroke-width="1.5"/></svg>
        </div>
        <div class="contact__line">www.lorvextilo.com
          <svg viewBox="0 0 24 24"><circle cx="12" cy="12" r="10"/><path d="M2 12h20M12 2c3 3 3 17 0 20M12 2c-3 3-3 17 0 20" fill="none" stroke="var(--magenta)" stroke-width="1.5"/></svg>
        </div>
      </div>
    </div>
  </section>

  <section class="card card--back">
    <div class="back-mark">
      <span class="back-mark__name">LORVEX TILO</span>
    </div>
    <div class="back-url">www.tilorise.com</div>
  </section>
</body>
</html>
```